Business card for a new cabinet shop company named Veloran Cabinets for high end cabinets

Design a business card, thinking dark rich green with colours to speak of high end luxury ie; cream, gold, black possibly

Mitchell Tarrowby
Director Craftsman
Email: info@veloranjoinery-example.com.au
Instagram : @veloran.cabinets

```html
<!DOCTYPE html>
<html lang="en">
<head>
<meta charset="utf-8">
<title>Veloran Cabinets – Business Card</title>
<link rel="stylesheet" href="https://fonts.googleapis.com/css2?family=Arimo:wght@400;700&display=swap">
<style>
  :root {
    --backdrop: #d9d9d9;
    --paper: #fbf8f1;
    --ink: #2f3a33;
    --muted: #5f6b63;
    --gold: #c8a35f;
    --rule: #cfc8b8;
    --card-dark: #14301f;
    --card-dark-top: #1b3d29;
    --deboss: #2f5a40;
  }
  * { box-sizing: border-box; margin: 0; padding: 0; }
  html, body {
    width: 1200px; height: 1200px; overflow: hidden;
    background: var(--backdrop);
    font-family: "Arimo", Arial, sans-serif;
  }
  .canvas { position: relative; width: 1200px; height: 1200px; }

  .card {
    position: absolute;
    width: 687px; height: 393px;
    border-radius: 20px;
    overflow: hidden;
  }
  .card--front { left: 267px; top: 159px; background: var(--paper); }
  .card--back {
    left: 262px; top: 653px;
    background: linear-gradient(180deg, var(--card-dark-top), var(--card-dark));
  }

  .brand-name {
    position: absolute;
    right: 52px; top: 68px;
    font-size: 40px; font-weight: 400;
    color: var(--gold);
    letter-spacing: 0.5px;
    white-space: nowrap;
  }

  .holder { position: absolute; left: 47px; top: 228px; }
  .holder__name { font-size: 26px; font-weight: 700; color: var(--gold); line-height: 1.2; }
  .holder__role { font-size: 15px; color: var(--muted); margin-top: 2px; }

  .divider {
    position: absolute; left: 47px; right: 48px; top: 289px;
    height: 1px; background: var(--rule);
  }

  .contacts { position: absolute; left: 47px; top: 300px; list-style: none; }
  .contacts li {
    display: flex; align-items: center; gap: 8px;
    font-size: 15px; color: var(--ink); line-height: 20px;
    white-space: nowrap;
  }
  .contacts svg { width: 14px; height: 14px; flex: none; }

  .website {
    position: absolute; right: 48px; top: 301px;
    font-size: 15px; color: var(--ink);
    white-space: nowrap;
  }

  .back-name {
    position: absolute; left: 0; right: 0; top: 168px;
    text-align: center;
    font-size: 50px; font-weight: 400;
    color: var(--deboss);
    letter-spacing: 1px;
  }
</style>
</head>
<body>
<main class="canvas">
  <section class="card card--front" aria-label="Card front">
    <div class="brand-name">Veloran Cabinets</div>

    <div class="holder">
      <p class="holder__name">Mitchell Tarrowby</p>
      <p class="holder__role">Director Craftsman</p>
    </div>

    <div class="divider"></div>

    <ul class="contacts">
      <li>
        <svg viewBox="0 0 14 14" aria-hidden="true">
          <rect x="1" y="3" width="12" height="8" fill="var(--gold)"/>
          <path d="M1 3 L7 8 L13 3" fill="none" stroke="#fff" stroke-width="1.2"/>
        </svg>
        info@veloranjoinery-example.com.au
      </li>
      <li>
        <svg viewBox="0 0 14 14" aria-hidden="true">
          <circle cx="7" cy="7" r="6" fill="var(--gold)"/>
        </svg>
        @veloran.cabinets
      </li>
    </ul>

    <p class="website">www.veloranjoinery-example.com.au</p>
  </section>

  <section class="card card--back" aria-label="Card back">
    <div class="back-name">Veloran Cabinets</div>
  </section>
</main>
</body>
</html>
```